Road Construction Company needs business cards

We would like a new business card designed for our business.

We're a road construction company based in Qld, Australia.

Can the business card please have the following information on it.

Name: Warren Halbeck
Position: General Manager
Phone: 0472 915 348
Email: Warren.halbeck@tovrin.com.au
Address: 87 Marrow Ave, Pendlebay, QLD, 4023
Website: www.tovrin.com.au

Visually we'd like the card to be professional and simple.

Attached is our logo.

Our website is www.tovrin.com.au

Target Market(s)

Men aged 25-60

Contact Information for Business Card

As listed in project description

Font styles to use
Serif

Requirements
Must have
• Large logo on back of card

```html
<!DOCTYPE html>
<html lang="en">
<head>
<meta charset="utf-8">
<title>Tovrin Road Construction – Business Card</title>
<link rel="stylesheet" href="https://fonts.googleapis.com/css2?family=Archivo:wght@400;500;700;800&display=swap">
<style>
  :root {
    --backdrop: #e4e6e9;
    --card-white: #ffffff;
    --card-shade: #eceef0;
    --card-black: #0c0c0d;
    --pattern-tone: #16181c;
    --brand-navy: #1659a8;
    --brand-sky: #2a8fd6;
    --ink: #3a3c40;
    --rule: #1d5cae;
    --divider: #8fb6e0;
  }
  * { margin: 0; padding: 0; box-sizing: border-box; }
  html, body { width: 1200px; height: 900px; overflow: hidden; }
  body {
    background: var(--backdrop);
    font-family: "Archivo", Arial, sans-serif;
    display: flex;
    flex-direction: column;
    align-items: center;
    justify-content: center;
    gap: 60px;
  }
  .card {
    position: relative;
    width: 630px;
    height: 360px;
    border-radius: 3px;
    overflow: hidden;
    box-shadow: 0 10px 28px rgba(0,0,0,.22);
  }

  /* Back */
  .card-back { background: var(--card-black); }
  .back-pattern {
    position: absolute; inset: 0;
    background: radial-gradient(ellipse at 60% 40%, var(--pattern-tone), var(--card-black) 75%);
  }
  .back-name {
    position: absolute;
    left: 0; right: 0; top: 50%;
    transform: translateY(-50%);
    text-align: center;
    font-weight: 800;
    font-size: 58px;
    letter-spacing: 4px;
    color: var(--brand-navy);
  }

  /* Front */
  .card-front { background: linear-gradient(135deg, var(--card-white) 40%, var(--card-shade)); }
  .front-name {
    position: absolute;
    top: 52px; left: 190px;
    font-weight: 800;
    font-size: 56px;
    letter-spacing: 3px;
    color: var(--brand-navy);
  }
  .front-sector {
    position: absolute;
    top: 118px; left: 196px;
    font-weight: 700;
    font-size: 11px;
    letter-spacing: 11.5px;
    color: var(--brand-sky);
  }
  .person {
    position: absolute;
    top: 190px; left: 40px;
  }
  .person-name {
    font-weight: 800;
    font-size: 17px;
    letter-spacing: .5px;
    color: var(--brand-sky);
    text-transform: uppercase;
  }
  .person-role {
    margin-top: 3px;
    font-size: 14px;
    color: var(--ink);
  }
  .person-rule {
    position: absolute;
    top: 246px; left: 0;
    width: 480px; height: 1.5px;
    background: var(--rule);
  }
  .contact-list {
    position: absolute;
    top: 260px; left: 52px;
    list-style: none;
  }
  .contact-list li {
    display: flex; align-items: center; gap: 8px;
    font-size: 13.5px;
    color: var(--ink);
    line-height: 26px;
  }
  .contact-list svg { width: 14px; height: 14px; fill: none; stroke: var(--brand-navy); stroke-width: 2; }
  .address {
    position: absolute;
    top: 262px; left: 380px;
    padding-left: 16px;
    border-left: 1px solid var(--divider);
    font-size: 13.5px;
    line-height: 26px;
    color: var(--ink);
  }
</style>
</head>
<body>

  <section class="card card-back" aria-label="Card back">
    <div class="back-pattern" role="img" aria-label="Dark repeating brand pattern background"></div>
    <div class="back-name">TOVRIN</div>
  </section>

  <section class="card card-front" aria-label="Card front">
    <div class="front-name">TOVRIN</div>
    <div class="front-sector">ROAD CONSTRUCTION</div>

    <div class="person">
      <div class="person-name">Warren Halbeck</div>
      <div class="person-role">General Manager</div>
    </div>
    <div class="person-rule"></div>

    <ul class="contact-list">
      <li>
        <svg viewBox="0 0 24 24"><path d="M5 3h4l2 5-3 2a11 11 0 0 0 6 6l2-3 5 2v4a2 2 0 0 1-2 2A17 17 0 0 1 3 5a2 2 0 0 1 2-2z"/></svg>
        0472 915 348
      </li>
      <li>
        <svg viewBox="0 0 24 24"><circle cx="12" cy="12" r="9"/><path d="M3 12h18M12 3c3 3 3 15 0 18M12 3c-3 3-3 15 0 18"/></svg>
        www.tovrin.com.au
      </li>
      <li>
        <svg viewBox="0 0 24 24"><rect x="3" y="6" width="18" height="13" rx="1"/><path d="M3 7l9 7 9-7"/></svg>
        Warren.halbeck@tovrin.com.au
      </li>
    </ul>

    <address class="address" style="font-style:normal">
      87 Marrow Ave<br>
      Pendlebay, QLD, 4023
    </address>
  </section>

</body>
</html>
```